Business card design for Virtual Assistance company

I need a business card designed for my virtual assistance company. We are a small company who services primarily C-level executive clients. The card needs to be double sided with the following contact information on the back:
Melissa Thornbury
Owner/CEO
info@rkpadvisory.net
www.rkpadvisory.net
555.302.9817

The front side should just have the company name incorporated: "RKP Advisory" and "virtual assistance"

The card should be simplistic, but eye catching and should speak to high level executives. Our primary focus areas consist of executive assistance and government contracting.

Target Market(s)

CEOs and executives

Contact Information for Business Card

see project description. phone, email, website.

Colors

Designer to choose only greyscale colors for use in the design.

```html
<!DOCTYPE html>
<html lang="en">
<head>
<meta charset="utf-8">
<title>RKP Advisory – Business Card</title>
<link href="https://fonts.googleapis.com/css2?family=Cormorant+Garamond:wght@500;700&family=Montserrat:wght@300;400&display=swap" rel="stylesheet">
<style>
  :root {
    --page: #2b2b2b;
    --card-black: #0e0e0e;
    --pattern-light: #2a2a2a;
    --pattern-dark: #080808;
    --card-white: #ffffff;
    --band: #1c1c1c;
    --ink: #1a1a1a;
    --ink-soft: #3a3a3a;
    --on-dark: #ffffff;
    --on-dark-soft: #cfcfcf;
  }
  * { margin: 0; padding: 0; box-sizing: border-box; }
  html, body { width: 1200px; height: 875px; overflow: hidden; }
  body {
    background: var(--page);
    position: relative;
    font-family: "Montserrat", sans-serif;
  }
  .card {
    position: absolute;
    width: 525px;
    height: 300px;
    border-radius: 18px;
    overflow: hidden;
  }

  /* Back side: black card */
  .card-back {
    left: 55px;
    top: 190px;
    background: var(--card-black);
  }
  .card-back .pattern {
    position: absolute;
    inset: 0;
    background: linear-gradient(115deg, var(--pattern-light) 0%, var(--pattern-dark) 55%, var(--pattern-light) 100%);
  }
  .card-back .brand-name {
    position: absolute;
    right: 42px;
    top: 60px;
    font-family: "Cormorant Garamond", serif;
    font-weight: 500;
    font-size: 30px;
    color: var(--on-dark);
    letter-spacing: 0.5px;
  }

  /* Front side: white card */
  .card-front {
    left: 620px;
    top: 385px;
    background: var(--card-white);
  }
  .card-front .heading {
    position: absolute;
    left: 0; right: 0;
    top: 38px;
    text-align: center;
  }
  .card-front .company {
    font-family: "Cormorant Garamond", serif;
    font-weight: 500;
    font-size: 50px;
    line-height: 1;
    color: var(--ink);
  }
  .card-front .tagline {
    margin-top: 8px;
    font-family: "Cormorant Garamond", serif;
    font-weight: 500;
    font-size: 17px;
    letter-spacing: 1.5px;
    color: var(--ink-soft);
  }
  .card-front .band {
    position: absolute;
    left: 0; right: 0;
    top: 168px;
    height: 88px;
    background: var(--band);
    display: flex;
    align-items: center;
    justify-content: center;
    gap: 18px;
  }
  .person { text-align: right; }
  .person .name {
    font-family: "Cormorant Garamond", serif;
    font-weight: 700;
    font-size: 21px;
    color: var(--on-dark);
  }
  .person .role {
    font-size: 10px;
    font-weight: 300;
    color: var(--on-dark-soft);
  }
  .divider {
    width: 1px;
    height: 60px;
    background: var(--on-dark-soft);
  }
  .contacts { list-style: none; }
  .contacts li {
    display: flex;
    align-items: center;
    gap: 7px;
    font-size: 10.5px;
    font-weight: 300;
    color: var(--on-dark);
    line-height: 19px;
  }
  .contacts svg { width: 10px; height: 10px; fill: none; stroke: var(--on-dark); stroke-width: 1.6; }
</style>
</head>
<body>

<section class="card card-back" aria-label="Card back">
  <div class="pattern" role="img" aria-label="Repeating gloss monogram pattern in black on black"></div>
  <div class="brand-name">RKP Advisory</div>
</section>

<section class="card card-front" aria-label="Card front">
  <div class="heading">
    <div class="company">RKP Advisory</div>
    <div class="tagline">VIRTUAL ASSISTANCE</div>
  </div>
  <div class="band">
    <div class="person">
      <div class="name">Melissa Thornbury</div>
      <div class="role">Owner/CEO</div>
    </div>
    <div class="divider"></div>
    <ul class="contacts">
      <li>
        <svg viewBox="0 0 10 10"><path d="M2 1 L4 3 L3 4 Q4.5 6 6 7 L7 6 L9 8 L8 9 Q4 9 1 5 Q1 2 2 1 Z"/></svg>
        555.302.9817
      </li>
      <li>
        <svg viewBox="0 0 10 10"><rect x="1" y="2" width="8" height="6"/><path d="M1 2 L5 5.5 L9 2"/></svg>
        info@rkpadvisory.net
      </li>
      <li>
        <svg viewBox="0 0 10 10"><circle cx="5" cy="5" r="4"/><path d="M1 5 H9 M5 1 Q2.5 5 5 9 M5 1 Q7.5 5 5 9"/></svg>
        www.rkpadvisory.net
      </li>
    </ul>
  </div>
</section>

</body>
</html>
```